Business Card Design

We need a business card designed for a new company based in Melbourne called Kvt solutions. Kvt solutions provides management consulting specialising in the health and social services sector.

Kvt solutions offer a unique set of specialist skills │dealing with all levels of government │ unique communication skills│intimate knowledge of the health sector │solutions tailored to unique circumstances.

Kvt solutions takes on a select number of clients at any one time, this ensures that your organisation receives the attention required. On larger projects, Kvt solutions join up with other consultants to bring specialist skills to a project.
Updates

This is the first time I have used Pixel Harbor and thank you all for responding. The variation is amazing and makes it hard to decide. I have to ask some of my friends to give me their views. The response is fantastic. The one I pick will basically be the most visually appealing

Industry/Entity Type

Management Consulting

Contact Information for Business Card

Martin Oakes, Principal, Kvt solutions, 14 Wexcombe Ave, Larkdale VIC 3189, 0417 382 914, martino@kvtsolutions-example.com.au, www.kvtsolutions-example.com.au

```html
<!DOCTYPE html>
<html lang="en">
<head>
<meta charset="utf-8">
<title>Kvt solutions – Business Card</title>
<link rel="stylesheet" href="https://fonts.googleapis.com/css2?family=Zilla+Slab:wght@500;700&family=Open+Sans:wght@400;600&display=swap">
<style>
  :root {
    --stage: #e4e2df;
    --card-red: #c01f2e;
    --card-red-deep: #a51725;
    --ink-dark: #2a1013;
    --card-black: #050505;
    --line-grey: #6d6d6d;
    --white: #ffffff;
    --card-w: 640px;
    --card-h: 366px;
  }
  * { box-sizing: border-box; margin: 0; padding: 0; }
  html, body {
    width: 1200px; height: 914px; overflow: hidden;
    background: var(--stage);
  }
  .canvas {
    width: 1200px; height: 914px;
    display: flex; flex-direction: column;
    align-items: center; justify-content: center; gap: 60px;
  }
  .card {
    position: relative;
    width: var(--card-w); height: var(--card-h);
    overflow: hidden;
    box-shadow: 0 6px 18px rgba(0,0,0,0.18);
  }

  /* Front */
  .card--front { background: var(--card-red); }
  .front__texture {
    position: absolute; left: 0; right: 0; height: 90px;
  }
  .front__texture--top {
    top: 0;
    background: linear-gradient(to bottom, var(--card-red-deep), rgba(165,23,37,0));
  }
  .front__texture--bottom {
    bottom: 0;
    background: linear-gradient(to top, var(--card-red-deep), rgba(165,23,37,0));
  }
  .front__identity {
    position: absolute; left: 128px; top: 108px;
  }
  .front__name {
    font-family: 'Zilla Slab', serif;
    font-weight: 700;
    font-size: 24px; line-height: 1.1; color: var(--ink-dark);
  }
  .front__role {
    font-family: 'Zilla Slab', serif;
    font-weight: 500;
    font-size: 15px; line-height: 1.2; color: var(--ink-dark);
    letter-spacing: 0.4px;
  }
  .front__brand {
    margin-top: 10px;
    font-family: 'Open Sans', sans-serif;
    font-weight: 600;
    font-size: 40px; line-height: 1.05;
    color: var(--white);
  }
  .front__tagline {
    margin-top: 10px;
    font-family: 'Zilla Slab', serif;
    font-weight: 700;
    font-size: 13px; color: var(--white);
    text-transform: uppercase; letter-spacing: 0.8px;
  }

  /* Back */
  .card--back { background: var(--card-black); }
  .back__edge {
    position: absolute; left: 0; top: 0; bottom: 0; width: 14px;
    background: var(--card-red);
  }
  .back__texture {
    position: absolute; left: 14px; bottom: 0; width: 170px; height: 120px;
    background: radial-gradient(ellipse at 0% 100%, rgba(192,31,46,0.35), rgba(192,31,46,0) 70%);
  }
  .back__rail {
    position: absolute; left: 0; top: 0;
  }
  .contact-list {
    position: absolute; left: 100px; top: 48px;
    list-style: none;
    font-family: 'Open Sans', sans-serif;
    font-size: 17px; color: var(--white);
  }
  .contact-list li { height: 40px; line-height: 24px; white-space: nowrap; }
</style>
</head>
<body>
<main class="canvas">

  <section class="card card--front" aria-label="Business card front">
    <div class="front__texture front__texture--top" role="img" aria-label="Faint cross grid pattern band"></div>
    <div class="front__texture front__texture--bottom" role="img" aria-label="Faint cross grid pattern band"></div>
    <div class="front__identity">
      <p class="front__name">Martin Oakes</p>
      <p class="front__role">Principal</p>
      <p class="front__brand">Kvt solutions</p>
      <p class="front__tagline">Health &amp; Social Services Consulting</p>
    </div>
  </section>

  <section class="card card--back" aria-label="Business card back">
    <div class="back__edge"></div>
    <div class="back__texture" role="img" aria-label="Faint red cross grid pattern"></div>
    <svg class="back__rail" width="100" height="366" viewBox="0 0 100 366" aria-hidden="true">
      <line x1="62" y1="30" x2="62" y2="200" stroke="var(--line-grey)" stroke-width="2"/>
      <circle cx="62" cy="60" r="12" fill="var(--card-red)"/>
      <path d="M62 67 C58 62 57 60 57 57.5 a5 5 0 0 1 10 0 C67 60 66 62 62 67Z" fill="none" stroke="var(--white)" stroke-width="1.6"/>
      <circle cx="62" cy="57.5" r="1.6" fill="var(--white)"/>
      <circle cx="62" cy="100" r="12" fill="var(--card-red)"/>
      <rect x="58" y="93" width="8" height="14" rx="1.5" fill="none" stroke="var(--white)" stroke-width="1.6"/>
      <line x1="61" y1="104.5" x2="63" y2="104.5" stroke="var(--white)" stroke-width="1.4"/>
      <circle cx="62" cy="140" r="12" fill="var(--card-red)"/>
      <rect x="55.5" y="135.5" width="13" height="9" fill="none" stroke="var(--white)" stroke-width="1.5"/>
      <path d="M55.5 135.5 L62 141 L68.5 135.5" fill="none" stroke="var(--white)" stroke-width="1.5"/>
      <circle cx="62" cy="180" r="12" fill="var(--card-red)"/>
      <circle cx="62" cy="180" r="6.5" fill="none" stroke="var(--white)" stroke-width="1.5"/>
      <ellipse cx="62" cy="180" rx="2.8" ry="6.5" fill="none" stroke="var(--white)" stroke-width="1.2"/>
      <line x1="55.5" y1="180" x2="68.5" y2="180" stroke="var(--white)" stroke-width="1.2"/>
    </svg>
    <ul class="contact-list">
      <li>Kvt solutions, 14 Wexcombe Ave, Larkdale VIC 3189.</li>
      <li>0417 382 914</li>
      <li>martino@kvtsolutions-example.com.au</li>
      <li>www.kvtsolutions-example.com.au</li>
    </ul>
  </section>

</main>
</body>
</html>
```